Bramblewood Joinery Website

My client Bramblewood Joinery is looking for a redesign for a Word Press Website. Their current site is at www.bramblewoodjoinery.example They are a custom cabinet company, but also create bathroom, living room, bar and entertainment and bedroom cabinets too. They would like a design that emulates the master craftsman work they do yet a contemporary style.

Their current site was designed using Flash elements.

Target Market(s)

Home owners and builders of high end homes

Industry/Entity Type

Entertainment

Font styles to use
Serif
Decorative

Requirements
Must have
• Must show their work and logo using a contemporary style.
Nice to have
• Sliders that showcase their projects.

```html
<!DOCTYPE html>
<html lang="en">
<head>
<meta charset="utf-8">
<title>Bramblewood Joinery</title>
<link href="https://fonts.googleapis.com/css2?family=Noto+Serif:ital,wght@0,400;0,700;1,400&family=Didact+Gothic&family=Open+Sans:wght@600;700&display=swap" rel="stylesheet">
<style>
:root{
  --green:#2aa432;
  --green-dark:#1f8a27;
  --ink:#111;
  --bar:#1b1b1b;
  --band:#202020;
  --footer:#16171a;
  --text:#444;
  --muted:#bcbcbc;
  --white:#fff;
}
*{margin:0;padding:0;box-sizing:border-box}
html,body{width:1110px;height:1200px;overflow:hidden;background:var(--white)}
body{position:relative;font-family:"Didact Gothic",sans-serif;color:var(--text)}
.abs{position:absolute}

.topbar{left:0;top:0;width:1110px;height:28px;background:var(--bar)}
.toplinks{right:210px;top:7px;display:flex;gap:14px;font:600 12px "Open Sans",sans-serif;color:#eee}
.toplinks span.sep{color:#888}
.topsocial{left:910px;top:6px;display:flex;gap:12px}
.topsocial i{display:block;width:14px;height:14px;border-radius:3px;background:#ddd}

.header{left:0;top:28px;width:1110px;height:105px;background:var(--white)}
.brand-badge{left:102px;top:30px;width:122px;height:130px;border-radius:0 0 61px 61px;background:var(--white);z-index:3;display:flex;align-items:center;justify-content:center}
.brand-badge .ring{width:112px;height:112px;border-radius:50%;border:4px solid var(--ink);display:flex;align-items:center;justify-content:center;text-align:center;font:700 13px/1.25 "Noto Serif",serif;color:var(--ink)}
.nav{left:342px;top:67px;display:flex;align-items:center;gap:26px;font:400 15px "Noto Serif",serif;color:var(--ink)}
.nav .active{background:var(--green);color:var(--white);padding:6px 11px;border-radius:2px}

.hero{left:0;top:133px;width:1110px;height:422px;background:linear-gradient(180deg,#cdbfae 0%,#e9e4dc 30%,#d9d4cc 60%,#6b4b36 90%,#4e3526 100%)}
.hero-line{font:italic 400 31px/53px "Noto Serif",serif;color:var(--white);padding:0 13px}
.hero-line.one{left:333px;top:277px;background:rgba(34,160,40,.88)}
.hero-line.two{left:304px;top:335px;background:rgba(28,28,28,.88);padding:0 17px}
.dots{left:510px;top:520px;display:flex;gap:7px}
.dots i{width:11px;height:11px;border-radius:50%;background:#ddd}
.dots i.on{background:#222}
.hero-rule{left:0;top:555px;width:1110px;height:4px;background:var(--green)}

.band{left:0;top:559px;width:1110px;height:126px;background:linear-gradient(#2a2a2a,#151515)}
.pill{top:581px;width:200px;height:79px;border-radius:40px 40px 40px 0;border-bottom-right-radius:40px;background:linear-gradient(#fff,#d9d9d9);display:flex;align-items:center;gap:10px;padding-left:4px}
.pill .disc{width:72px;height:72px;border-radius:50%;background:var(--green);border:3px solid #fff;display:flex;align-items:center;justify-content:center;flex:none}
.pill .label{font:400 16px/19px "Noto Serif",serif;color:var(--ink)}
.pill .label b{display:block;font-weight:400;color:var(--green)}

.who-title{left:107px;top:728px;font:400 25px "Noto Serif",serif;color:var(--ink)}
.who-copy{left:107px;top:771px;width:566px;font-size:14.2px;line-height:23.2px;color:#444}

.video-tag{left:698px;top:720px;width:163px;height:23px;background:var(--green);font:700 18px/23px "Noto Serif",serif;color:var(--white);padding-left:11px}
.video-frame{left:712px;top:744px;width:296px;height:164px;background:#fff;box-shadow:0 10px 10px -6px rgba(0,0,0,.45)}
.video-screen{left:720px;top:751px;width:281px;height:153px;background:linear-gradient(135deg,#6e6a66 0%,#b8b2a8 45%,#e6e2dc 70%,#5a3d2c 100%)}
.video-controls{left:720px;top:889px;width:281px;height:15px;background:#1a1a1a}
.video-progress{left:720px;top:887px;width:52px;height:2px;background:#c00}
.play{left:833px;top:799px;width:60px;height:38px;background:#111}

.footer{left:0;top:945px;width:1110px;height:255px;background:var(--footer)}
.f-head{top:985px;font:600 15.5px "Open Sans",sans-serif;color:var(--white)}
.sitemap{left:113px;top:1020px;list-style:none;font-size:13px;line-height:20.4px;color:var(--muted)}
.sitemap li::before{content:"• ";color:#ddd}
.contact{left:299px;top:1020px;font-size:13px;line-height:20.4px;color:var(--muted)}
.contact .row{display:flex;gap:7px;margin-bottom:11px}
.contact svg{flex:none;margin-top:4px}
.social{left:602px;top:1028px;display:flex;gap:9px}
.social i{width:25px;height:25px;border-radius:50%}
.f-brand{left:599px;top:1073px;display:flex;align-items:center;gap:8px;font:700 17px "Open Sans",sans-serif;color:#eee}
.f-brand i{width:14px;height:14px;border-radius:50%;background:#888}
.copyright{left:602px;top:1107px;font-size:13px;line-height:18.5px;color:var(--muted)}
.f-seal{left:855px;top:1014px;width:115px;height:120px;border-radius:50%;border:4px solid #6a6a6a;display:flex;align-items:center;justify-content:center;text-align:center;font:700 13px/1.3 "Noto Serif",serif;color:#6a6a6a}
</style>
</head>
<body>
<div class="abs topbar"></div>
<div class="abs toplinks"><span>Getting Started</span><span class="sep">|</span><span>Who We Are</span><span class="sep">|</span><span>Contact Us</span></div>
<div class="abs topsocial"><i></i><i></i><i></i><i></i></div>

<header class="abs header"></header>
<div class="abs brand-badge"><div class="ring">Bramblewood<br>Joinery</div></div>
<nav class="abs nav">
  <span class="active">HOME</span><span>CUSTOMER EXPERIENCE</span><span>PROFESSIONAL</span><span>PORTFOLIO</span><span>CABINET HARDWARE</span>
</nav>

<section class="abs hero" role="img" aria-label="Bright white custom kitchen with stainless range, sunflowers by the window and a wooden floor"></section>
<div class="abs hero-line one">Kansas City's Premier Custom</div>
<div class="abs hero-line two">Kitchen Cabinet Design Company</div>
<div class="abs dots"><i></i><i class="on"></i><i></i><i></i></div>
<div class="abs hero-rule"></div>

<section class="abs band"></section>
<div class="abs pill" style="left:122px">
  <span class="disc"><svg width="30" height="40" viewBox="0 0 30 40" fill="none" stroke="#fff" stroke-width="3"><path d="M4 3h22v8a11 11 0 0 1-22 0z"/><path d="M15 22v14M7 37h16"/></svg></span>
  <span class="label">BAR<b>DESIGNING</b></span>
</div>
<div class="abs pill" style="left:343px">
  <span class="disc"><svg width="30" height="40" viewBox="0 0 30 40" fill="none" stroke="#fff" stroke-width="3"><rect x="4" y="3" width="22" height="6"/><path d="M7 9v29M23 9v29M7 24h16"/></svg></span>
  <span class="label">LIVING ROOM<b>CABINETS</b></span>
</div>
<div class="abs pill" style="left:563px">
  <span class="disc"><svg width="44" height="30" viewBox="0 0 44 30" fill="#fff"><rect x="2" y="4" width="4" height="24"/><rect x="6" y="17" width="36" height="6"/><rect x="38" y="17" width="4" height="11"/><circle cx="12" cy="12" r="4"/><rect x="18" y="9" width="22" height="7" rx="2"/></svg></span>
  <span class="label">BEDROOM<b>CABINETS</b></span>
</div>
<div class="abs pill" style="left:784px">
  <span class="disc"><svg width="42" height="38" viewBox="0 0 42 38" fill="none" stroke="#fff" stroke-width="3"><path d="M8 20V6a4 4 0 0 1 8 0"/><path d="M3 20h36v5a8 8 0 0 1-8 8H11a8 8 0 0 1-8-8z" fill="#fff"/><path d="M11 33l-2 4M31 33l2 4"/></svg></span>
  <span class="label">BATHROOM<b>CABINETS</b></span>
</div>

<h2 class="abs who-title">WHO WE ARE</h2>
<p class="abs who-copy">Established in 1966, Bramblewood Joinery has long stood as one of the Midwest's most renowned makers of custom cabinets and fixtures. Our handcrafted, award-winning creations have been chosen by hundreds of noteworthy homebuilders. And while we custom build cabinets, we built our business around the belief that our customers absolutely, unequivocally come first. From day one, our mission has been to help turn the houses that people live in to the homes they've always dreamed of.</p>

<div class="abs video-frame"></div>
<div class="abs video-screen" role="img" aria-label="Video still of a white kitchen with a wall oven and cabinetry"></div>
<div class="abs video-controls"></div>
<div class="abs video-progress"></div>
<div class="abs play"><svg width="60" height="38" viewBox="0 0 60 38"><path d="M25 11l14 8-14 8z" fill="#fff"/></svg></div>
<div class="abs video-tag">Featured Video</div>

<footer class="abs footer"></footer>
<h3 class="abs f-head" style="left:113px">Site Map</h3>
<ul class="abs sitemap">
  <li>Home</li><li>Who We Are</li><li>Getting Started</li><li>Customer Experience</li><li>Professional</li><li>Portfolio</li>
</ul>
<h3 class="abs f-head" style="left:299px">Contact us</h3>
<div class="abs contact">
  <div class="row"><svg width="12" height="16" viewBox="0 0 12 16"><path d="M6 0a6 6 0 0 1 6 6c0 4-6 10-6 10S0 10 0 6a6 6 0 0 1 6-6z" fill="#888"/><circle cx="6" cy="6" r="2" fill="#16171a"/></svg><span>Bramblewood Joinery Dana Hollis<br>4820 Orchard Lane Fairview,<br>MO 64000</span></div>
  <div class="row"><svg width="14" height="14" viewBox="0 0 14 14"><path d="M3 0l3 3-2 2c1 2 3 4 5 5l2-2 3 3-2 3C6 14 0 8 0 3z" fill="#888"/></svg><span>555.014.2300</span></div>
  <div class="row"><svg width="16" height="11" viewBox="0 0 16 11"><rect width="16" height="11" fill="#888"/><path d="M0 0l8 6 8-6" stroke="#16171a" fill="none"/></svg><span>info@bramblewood.example</span></div>
</div>
<h3 class="abs f-head" style="left:602px">Follow Us</h3>
<div class="abs social"><i style="background:#2e4a8a"></i><i style="background:#1a8bc4"></i><i style="background:#e8621c"></i><i style="background:#b3172a"></i></div>
<div class="abs f-brand"><i></i>BRAMBLEWOOD</div>
<p class="abs copyright">copyright©2015.Bramblewood Joinery<br>All Rights Reserved</p>
<div class="abs f-seal">Bramblewood<br>Joinery</div>
</body>
</html>
```